Velk Partners Building Business Cards

We need a business card that reflects our business as "Solar Experts" in San Diego. Browse our website www.velkpartners.example our License needs to be displayed as "CSLB# 3867140" our phone number is (619) 555-0187

Save thousands on your electric bills and increase the value of your home while helping to protect the environment. Our solar installation experts will help you design the system that's right for you, using only the highest quality equipment that will look great and give you ideal performance. Our goal is to make you energy independent, and get your electric bill to 0.

Paul Osterby
(619) 555-0187
paul@velkpartners.example

Target Market(s)

Home owners in san diego looking for solar

Industry/Entity Type

Solar Energy

Contact Information for Business Card

Paul Osterby
(619) 555-0187
paul@velkpartners.example

Font styles to use
Other font styles liked:
• Use our logo font

Requirements
Must have
• License needs to be displayed as "CSLB# 3867140" our phone number is (619) 555-0187
Nice to have
• Real images of rooftop home solar in san diego
Should not have
• our business address

```html
<!DOCTYPE html>
<html lang="en">
<head>
<meta charset="utf-8">
<title>Velk Partners Building – Business Card</title>
<link rel="stylesheet" href="https://fonts.googleapis.com/css2?family=Source+Sans+3:wght@400;600;700&display=swap">
<style>
  :root {
    --navy: #1d3f7f;
    --navy-deep: #163266;
    --sun: #f7ae0a;
    --paper: #ffffff;
    --backdrop: #e9e6e1;
    --shadow: rgba(40, 30, 20, 0.22);
  }
  * { box-sizing: border-box; margin: 0; padding: 0; }
  html, body {
    width: 1200px; height: 950px; overflow: hidden;
    background: var(--backdrop);
    font-family: "Source Sans 3", "Helvetica Neue", Arial, sans-serif;
  }
  .sheet {
    width: 1200px; height: 950px;
    display: flex; flex-direction: column; align-items: center; justify-content: center;
    gap: 50px;
  }
  .card {
    position: relative;
    width: 700px; height: 400px;
    box-shadow: 0 10px 28px var(--shadow);
    overflow: hidden;
  }
  /* Front */
  .card--front { background: var(--paper); }
  .card__wave { position: absolute; inset: 0; width: 700px; height: 400px; }
  .brand {
    position: absolute; left: 48px; top: 140px;
    color: var(--navy); font-weight: 700; font-size: 31px; letter-spacing: -0.3px;
  }
  .person { position: absolute; left: 98px; top: 232px; }
  .person__name { color: var(--navy); font-weight: 600; font-size: 23px; line-height: 1.1; }
  .person__role { color: var(--sun); font-weight: 400; font-size: 15px; margin-top: 2px; }
  .contact {
    position: absolute; right: 36px; top: 132px;
    list-style: none; text-align: right;
    color: var(--paper); font-size: 16px; line-height: 27px;
  }
  .contact li { display: flex; align-items: center; justify-content: flex-end; gap: 9px; }
  .contact__icon { width: 15px; height: 15px; flex: none; }
  .contact__spacer { width: 15px; flex: none; }
  /* Back */
  .card--back { background: var(--sun); }
  .back__brand {
    position: absolute; inset: 0;
    display: flex; align-items: center; justify-content: center;
    color: var(--paper); font-weight: 700; font-size: 44px; letter-spacing: -0.3px;
  }
  .back__web {
    position: absolute; left: 26px; top: 50%;
    transform: translateY(-50%) rotate(180deg);
    writing-mode: vertical-rl;
    color: var(--paper); font-size: 13px; letter-spacing: 3px;
  }
</style>
</head>
<body>
<main class="sheet">
  <section class="card card--front" aria-label="Card front">
    <svg class="card__wave" viewBox="0 0 700 400" aria-hidden="true">
      <path d="M364 0 C314 120 504 220 454 400 L700 400 L700 0 Z" fill="var(--sun)"/>
      <path d="M384 0 C334 120 524 220 474 400 L700 400 L700 0 Z" fill="var(--navy)"/>
    </svg>
    <div class="brand">Velk Partners Building</div>
    <div class="person">
      <div class="person__name">Paul Osterby</div>
      <div class="person__role">CEO/Founder</div>
    </div>
    <ul class="contact">
      <li>CSLB# 3867140<span class="contact__spacer"></span></li>
      <li>(619) 555-0187
        <svg class="contact__icon" viewBox="0 0 16 16" aria-hidden="true"><path d="M4 1.5 L6.5 4.5 L5 6.5 C6 8.5 7.5 10 9.5 11 L11.5 9.5 L14.5 12 L13 14.5 C7 14 2 9 1.5 3 Z" fill="var(--sun)"/></svg>
      </li>
      <li>paul@velkpartners.example
        <svg class="contact__icon" viewBox="0 0 16 16" aria-hidden="true"><rect x="1" y="3" width="14" height="10" rx="1" fill="var(--sun)"/><path d="M1.5 3.5 L8 9 L14.5 3.5" stroke="var(--navy)" stroke-width="1.4" fill="none"/></svg>
      </li>
      <li>www.velkpartners.example
        <svg class="contact__icon" viewBox="0 0 16 16" aria-hidden="true"><circle cx="8" cy="8" r="7" fill="var(--sun)"/><path d="M1 8 H15 M8 1 C4.5 5 4.5 11 8 15 M8 1 C11.5 5 11.5 11 8 15" stroke="var(--navy)" stroke-width="1.1" fill="none"/></svg>
      </li>
    </ul>
  </section>

  <section class="card card--back" aria-label="Card back">
    <div class="back__web">www.velkpartners.example</div>
    <div class="back__brand">Velk Partners Building</div>
  </section>
</main>
</body>
</html>
```